Stylish new business card needed!

Hello everyone! I am in need of a new business card design for an alarm company here in Hurricane WV. I have all fonts, color codes and logos provided for you use! We are a young company and like the style of a clean sleek looking business card. Would like it double sided, one side holding the logo and the other with your design!
Target Market(s)
The people that are looking for the newest tech for home automation and security
Industry/Entity Type
Alarm services; Home automation
Contact Information for Business Card
Name of person; position (Sales; Installer); Phone Number (555.418.7260); Employee cell Number; Website (www.GuardedByVelk.example); Employee Email; Double sided
Look and feel
Each slider illustrates characteristics of the customer's brand and the style your logo design should communicate.

```html
<!DOCTYPE html>
<html lang="en">
<head>
<meta charset="utf-8">
<title>Velk Business Card</title>
<link href="https://fonts.googleapis.com/css2?family=Arimo:wght@400;700&display=swap" rel="stylesheet">
<style>
  :root {
    --stage: #2b2b2e;
    --card: #1f1e22;
    --card-back: #1c1b1f;
    --orange: #ec8a47;
    --grey: #9a9a9a;
    --white: #f2f2f2;
    --emboss: #141316;
  }
  * { box-sizing: border-box; margin: 0; padding: 0; }
  html, body {
    width: 1200px; height: 780px; overflow: hidden;
    background: var(--stage);
    font-family: "Arimo", Arial, sans-serif;
  }
  .canvas {
    position: relative; width: 1200px; height: 780px;
    display: flex; align-items: center; justify-content: center; gap: 50px;
  }
  .card {
    position: relative; width: 540px; height: 309px;
    overflow: hidden; border-radius: 3px;
    box-shadow: 0 10px 28px rgba(0,0,0,.45);
  }
  .card-front { background: var(--card); }
  .card-back { background: var(--card-back); display: flex; align-items: center; justify-content: center; }

  .brand { position: absolute; left: 34px; top: 26px; display: flex; align-items: center; gap: 10px; }
  .brand-dot { width: 30px; height: 30px; border-radius: 50%; background: var(--orange); }
  .brand-name { font-size: 58px; font-weight: 400; color: var(--grey); line-height: 1; letter-spacing: 2px; }

  .contacts { position: absolute; left: 34px; top: 118px; list-style: none; }
  .contacts li { display: flex; align-items: center; gap: 8px; font-size: 13.5px; color: var(--white); height: 19px; }
  .contacts svg { width: 11px; height: 11px; flex: none; }

  .divider { position: absolute; left: 240px; top: 213px; width: 262px; height: 1px; background: #d8d8d8; }
  .tab { position: absolute; right: 0; top: 199px; width: 28px; height: 30px; background: var(--orange); }

  .person { position: absolute; right: 40px; top: 176px; text-align: right; }
  .person-name { font-size: 24px; font-weight: 700; line-height: 1; }
  .person-name .first { color: var(--orange); }
  .person-name .last { color: var(--grey); }
  .person-role { position: absolute; right: 40px; top: 220px; font-size: 15px; font-weight: 700; color: var(--white); }

  .swoosh { position: absolute; left: 0; bottom: 0; width: 540px; height: 309px; }

  .back-name { font-size: 120px; font-weight: 400; color: var(--emboss); letter-spacing: 6px; text-shadow: 0 1px 0 rgba(255,255,255,.04); }
</style>
</head>
<body>
<main class="canvas">
  <section class="card card-front" aria-label="Card front">
    <svg class="swoosh" viewBox="0 0 540 309" aria-hidden="true">
      <path d="M0 258 C110 250 240 270 355 309 L0 309 Z" fill="var(--grey)"/>
      <path d="M0 236 C120 230 250 255 350 309 L355 309 C240 265 110 252 0 252 Z" fill="var(--orange)"/>
    </svg>

    <div class="brand">
      <span class="brand-dot"></span>
      <span class="brand-name">Velk</span>
    </div>

    <ul class="contacts">
      <li>
        <svg viewBox="0 0 12 12"><path d="M3 1 L5 3.5 L4 5 C4.8 6.6 5.6 7.4 7 8 L8.5 7 L11 9 L9.5 11 C5 10.5 1.5 7 1 2.5 Z" fill="var(--orange)"/></svg>
        555.418.7260
      </li>
      <li>
        <svg viewBox="0 0 12 12"><rect x="3" y="0.5" width="6" height="11" rx="1" fill="none" stroke="var(--orange)" stroke-width="1.2"/></svg>
        555.302.8841
      </li>
      <li>
        <svg viewBox="0 0 12 12"><circle cx="6" cy="6" r="5" fill="none" stroke="var(--orange)" stroke-width="1.2"/><path d="M1 6 H11 M6 1 C3.5 3.5 3.5 8.5 6 11 M6 1 C8.5 3.5 8.5 8.5 6 11" fill="none" stroke="var(--orange)" stroke-width="1"/></svg>
        www.GuardedByVelk.example
      </li>
      <li>
        <svg viewBox="0 0 12 12"><rect x="0.6" y="2" width="10.8" height="8" fill="none" stroke="var(--orange)" stroke-width="1.2"/><path d="M0.6 2 L6 6.5 L11.4 2" fill="none" stroke="var(--orange)" stroke-width="1.2"/></svg>
        info@GuardedByVelk.example
      </li>
    </ul>

    <div class="person">
      <p class="person-name"><span class="first">Marta</span> <span class="last">Lindqvist</span></p>
    </div>
    <div class="divider"></div>
    <p class="person-role">Sales; Installer</p>
    <div class="tab"></div>
  </section>

  <section class="card card-back" aria-label="Card back">
    <span class="back-name">Velk</span>
  </section>
</main>
</body>
</html>
```